Real Estate Webpage Design

We have an existing website: ferndaleestatecollective.com.au
We focus customised service mainly on Property Management and second-hand property sales.
We are not entirely happy about the current design and layout can stay roughly the same as the back end coding is linked to a CRM system.
We would like to see the design are more reachable to our clients and appearing.
Please check our Website Design Draft for more details.

Industry/Entity Type

Real estate Agency

Number of Pages Required

5+ page

Font styles to use
Sans Serif

Colors

Designer to choose colors to be used in the design.

```html
<!DOCTYPE html>
<html lang="en">
<head>
<meta charset="utf-8">
<title>Ferndale Estate Collective</title>
<link href="https://fonts.googleapis.com/css2?family=Lobster+Two:ital,wght@1,700&family=Oswald:wght@500;600&family=Poppins:wght@400;500;600;700&display=swap" rel="stylesheet">
<style>
:root{
  --gold:#d9a82e;
  --gold-dark:#b98a1c;
  --ink:#1c1c1c;
  --text:#444;
  --muted:#777;
  --line:#e3e3e3;
  --paper:#ffffff;
  --mist:#eef1f2;
  --night:#121212;
}
*{box-sizing:border-box;margin:0;padding:0}
html,body{width:1200px;height:4576px;overflow:hidden}
body{position:relative;background:var(--paper);font-family:'Poppins',sans-serif;color:var(--text)}
.abs{position:absolute}
.script{font-family:'Lobster Two',cursive;font-style:italic;font-weight:700;color:var(--ink)}
.btn{display:inline-flex;align-items:center;gap:12px;background:var(--gold);color:#fff;font-size:15px;font-weight:600;letter-spacing:1px;padding:0 10px 0 26px;height:50px;border-radius:25px}
.btn .dot{width:34px;height:34px;border-radius:50%;background:#fff;display:flex;align-items:center;justify-content:center}
.divider{width:60px;height:14px;display:block}

/* header */
.header{left:0;top:0;width:1200px;height:100px;background:#fff;z-index:2;box-shadow:0 2px 10px rgba(0,0,0,.08)}
.brand{left:110px;top:18px;display:flex;align-items:center;gap:12px}
.brand-mark{width:44px;height:44px;background:var(--gold)}
.brand-name{font-size:26px;font-weight:700;color:var(--ink);line-height:1}
.brand-sub{font-size:12px;color:var(--muted);display:block;margin-top:4px}
.topbar{right:50px;top:10px;display:flex;gap:14px;align-items:center;font-size:13px}
.topbar .pill{background:var(--ink);color:#fff;border-radius:16px;height:30px;display:flex;align-items:center;padding:0 16px;gap:8px}
.topbar .circle{width:30px;height:30px;border-radius:50%;background:var(--ink)}
.nav{right:50px;top:56px;display:flex;gap:40px;font-size:15px;font-weight:500;color:var(--ink)}
.nav .active{color:var(--gold)}

/* hero */
.hero{left:0;top:100px;width:1200px;height:620px;background:linear-gradient(180deg,#bcd6e8 0%,#e9e4da 45%,#b7a98f 70%,#6f8a4e 100%)}
.hero-title{left:0;width:1200px;top:190px;text-align:center;padding-left:40px}
.hero-title h1{font-family:'Lobster Two',cursive;font-style:italic;font-weight:700;font-size:100px;color:var(--ink);line-height:1}
.hero-title p{font-size:22px;letter-spacing:8px;color:var(--ink);margin-top:10px}
.hero-title .btn{margin-top:34px}
.arrow{width:50px;height:50px;border-radius:50%;background:var(--gold);display:flex;align-items:center;justify-content:center}

/* welcome */
.section-title{left:0;width:1200px;text-align:center;font-size:50px;line-height:1.2}
.who-img{left:170px;top:870px;width:350px;height:410px;background:linear-gradient(180deg,#b8cfe0 0%,#d8d4cc 50%,#8a7a66 100%)}
.who{left:590px;top:890px;width:460px}
.who h3{font-size:30px;font-weight:700;color:var(--ink)}
.who p{font-size:16px;line-height:1.6;margin-top:14px}

/* spanish band */
.band{left:0;top:1320px;width:1200px;height:640px;background:linear-gradient(120deg,#b9c9d8 0%,#c9a98e 40%,#a07a5a 60%,#6b8b4c 100%)}
.band-box{left:0;top:1320px;width:560px;height:640px;background:rgba(255,255,255,.96);padding:100px 40px 0 100px;text-align:right}
.band-box h2{font-size:48px;line-height:1.05}
.band-box p{font-size:16px;line-height:1.6;margin-top:26px;text-align:center}
.band-box .btn{margin-top:24px}

/* listings */
.tabs{left:300px;top:2140px;width:600px;display:flex;justify-content:space-between;font-size:14px;font-weight:600;color:var(--muted);letter-spacing:1px}
.tabs .on{color:var(--ink);border-bottom:3px solid var(--gold);padding-bottom:8px}
.card{top:2212px;width:320px;height:590px;background:#fff;box-shadow:0 4px 18px rgba(0,0,0,.15)}
.card.ghost{opacity:.45}
.card .photo{height:220px}
.card h4{font-family:'Oswald',sans-serif;font-weight:600;font-size:30px;letter-spacing:1px;text-align:center;color:var(--ink);margin-top:20px}
.card .addr{font-size:14px;text-align:center;margin-top:6px}
.feats{display:flex;justify-content:center;gap:18px;margin-top:18px}
.feat{width:56px;height:56px;border:2px solid var(--ink);border-radius:6px;display:flex;align-items:center;justify-content:center}
.card .insp{text-align:center;font-size:18px;font-weight:600;color:var(--ink);margin-top:18px}
.card .date{text-align:center;font-size:14px;margin-top:4px}
.card .price{text-align:center;font-size:38px;font-weight:700;color:var(--ink);margin-top:10px}
.card .bar{position:absolute;left:0;bottom:0;width:100%;height:44px;background:var(--gold);display:flex;justify-content:center;align-items:center;gap:22px}
.card .bar span{width:16px;height:16px;border:2px solid var(--ink);border-radius:3px}

/* team */
.team-bg{left:0;top:2860px;width:1200px;height:620px;background:var(--mist)}
.member{top:3080px;width:225px}
.member .portrait{width:225px;height:270px;background:linear-gradient(180deg,#4a4a4a,#2a2a2a)}
.member .info{text-align:center;font-size:16px;margin-top:-70px;position:relative;color:#fff}
.member .info b{display:block;font-size:18px}
.member .info small{font-size:11px;display:flex;justify-content:space-around;margin-top:6px}
.member.focus .portrait{background:#222}
.focus-card{left:0;top:20px;width:225px;text-align:center;color:#fff}
.focus-card h5{font-family:'Lobster Two',cursive;font-style:italic;font-weight:700;font-size:38px}
.focus-card p{font-size:12px;line-height:1.5;margin-top:6px}
.focus-card .rm{display:inline-block;background:var(--gold);border-radius:14px;font-size:11px;font-weight:600;padding:6px 18px;margin-top:16px}

/* testimonials */
.quote{top:3680px;width:460px;height:280px;background:#fff;box-shadow:0 4px 18px rgba(0,0,0,.14);border-radius:6px;text-align:center;padding:16px 36px 0}
.quote .mark{font-family:'Lobster Two',cursive;font-size:110px;color:var(--gold);line-height:1;height:80px}
.quote p{font-size:15px;line-height:1.6;margin-top:8px}
.quote .who-said{font-family:'Lobster Two',cursive;font-style:italic;font-weight:700;font-size:22px;color:var(--ink);margin-top:14px}
.dots{left:0;width:1200px;top:3990px;display:flex;justify-content:center;gap:10px}
.dots span{width:14px;height:14px;border-radius:50%;background:#d5d5d5}
.dots .on{background:var(--gold)}
.skyline{left:0;top:4030px;width:1200px;height:130px;background:linear-gradient(180deg,#ffffff 0%,#cfcfcf 100%)}

/* footer */
.footer{left:0;top:4160px;width:1200px;height:416px;background:var(--night);color:#ccc}
.f-brand{left:120px;top:120px;display:flex;align-items:center;gap:12px}
.f-brand .brand-name{color:#fff}
.f-social{left:140px;top:200px;display:flex;gap:12px}
.f-social span{width:34px;height:34px;border-radius:50%;border:2px solid #fff}
.f-col{top:110px;font-size:13px;line-height:1.85}
.f-col h6{font-size:18px;font-weight:700;color:#fff;margin-bottom:8px;letter-spacing:1px}
.contact-row{display:flex;gap:10px;align-items:flex-start;margin-bottom:8px;line-height:1.4}
.contact-row svg{flex:none;margin-top:2px}
.copy{left:0;width:1200px;top:370px;text-align:center;font-size:13px;color:#aaa;border-top:1px solid #333;padding-top:12px}
.chat{right:30px;top:4500px;width:54px;height:54px;border-radius:50%;background:var(--gold);display:flex;align-items:center;justify-content:center}
</style>
</head>
<body>

<header class="abs header">
  <div class="abs brand">
    <span class="brand-mark"></span>
    <span><span class="brand-name">Ferndale</span><span class="brand-sub">Estate Collective</span></span>
  </div>
  <div class="abs topbar">
    <span class="circle"></span><span class="circle"></span><span class="circle"></span>
    <span class="pill">hello@ferndaleestate.com.au</span>
    <span class="pill">02 5550 1942</span>
    <span>Eng ▾</span>
  </div>
  <nav class="abs nav">
    <span class="active">Home</span><span>About Us</span><span>Leasing</span><span>Buy</span><span>Sell</span><span>Our Team</span><span>Blog</span><span>Contact Us</span>
  </nav>
</header>

<section class="abs hero" role="img" aria-label="Modern townhouse apartments with balconies under a blue sky"></section>
<div class="abs arrow" style="left:20px;top:360px"><svg width="18" height="18" viewBox="0 0 18 18"><path d="M12 3 5 9l7 6" stroke="#fff" stroke-width="3" fill="none"/></svg></div>
<div class="abs arrow" style="right:20px;top:360px"><svg width="18" height="18" viewBox="0 0 18 18"><path d="M6 3l7 6-7 6" stroke="#fff" stroke-width="3" fill="none"/></svg></div>
<div class="abs hero-title">
  <h1>Ferndale</h1>
  <p>ESTATE COLLECTIVE</p>
  <span class="btn">LEARN MORE <span class="dot"><svg width="14" height="14" viewBox="0 0 14 14"><path d="M2 7h9M7 3l4 4-4 4" stroke="#d9a82e" stroke-width="2" fill="none"/></svg></span></span>
</div>

<h2 class="abs section-title script" style="top:760px">Welcome to Ferndale Estate Collective</h2>
<svg class="abs divider" style="left:570px;top:838px" viewBox="0 0 60 14"><rect x="0" y="6" width="60" height="2" fill="#d9a82e"/><rect x="24" y="2" width="12" height="10" fill="#fff" stroke="#d9a82e" stroke-width="2"/></svg>

<div class="abs who-img" role="img" aria-label="Photo collage of modern apartment buildings"></div>
<div class="abs who">
  <h3>Who is Ferndale?</h3>
  <p>Ferndale takes its name from a quiet valley of ferns, a place that feels like home. Buying a property is one of the most important steps for people, and Ferndale is a real estate company based in Harcourt, Rivervale.</p>
  <p>Being a portfolio sales agent and property manager, coupled with high-profile international real estate experience, Ferndale is a market leader in deep industry knowledge, ranging from landlord-tenant relationships to residential purchases.</p>
  <span class="btn" style="margin-top:26px">LEARN MORE <span class="dot"><svg width="14" height="14" viewBox="0 0 14 14"><path d="M2 7h9M7 3l4 4-4 4" stroke="#d9a82e" stroke-width="2" fill="none"/></svg></span></span>
</div>

<section class="abs band" role="img" aria-label="Row of brick townhouses along a green lawn and footpath"></section>
<div class="abs band-box">
  <h2 class="script">Ferndale – a valley<br>called “home”</h2>
  <p>Ferndale stands for a valley where you feel at home. Buying a property is one of the most important steps for people. Ferndale is a real estate company located in Harcourt, Rivervale.</p>
  <p style="margin-top:10px">Being a portfolio sales agent and property manager, coupled with high-profile international real estate experience, Ferndale is considered a market leader in the region.</p>
  <span class="btn">LEARN MORE <span class="dot"><svg width="14" height="14" viewBox="0 0 14 14"><path d="M2 7h9M7 3l4 4-4 4" stroke="#d9a82e" stroke-width="2" fill="none"/></svg></span></span>
</div>

<h2 class="abs section-title script" style="top:2020px">This Month At Ferndale Estate Collective</h2>
<svg class="abs divider" style="left:570px;top:2098px" viewBox="0 0 60 14"><rect x="0" y="6" width="60" height="2" fill="#d9a82e"/><rect x="24" y="2" width="12" height="10" fill="#fff" stroke="#d9a82e" stroke-width="2"/></svg>
<div class="abs tabs"><span class="on">FOR SALE</span><span>FOR LEASE</span><span>OPEN TIMES</span><span>SOLD</span><span>LEASED</span></div>

<div class="abs card ghost" style="left:-240px"><div class="photo" role="img" aria-label="Apartment block exterior" style="background:linear-gradient(#c4d6e4,#9aa6ae)"></div></div>
<div class="abs card ghost" style="left:1120px"><div class="photo" role="img" aria-label="Apartment block exterior" style="background:linear-gradient(#c4d6e4,#9aa6ae)"></div></div>

<article class="abs card" style="left:112px">
  <div class="photo" role="img" aria-label="High-rise apartments above a swimming pool" style="background:linear-gradient(#b4cde0,#6f9ec0 60%,#2e7fb5)"></div>
  <h4>HARCOURT</h4>
  <p class="addr">Level 3/77 Marlow Crescent Harcourt</p>
  <div class="feats"><span class="feat"><svg width="30" height="22" viewBox="0 0 30 22"><path d="M2 18V4M2 12h26v6M6 12V8h8v4" stroke="#1c1c1c" stroke-width="2" fill="none"/></svg></span><span class="feat"><svg width="30" height="22" viewBox="0 0 30 22"><path d="M3 10h24v4a6 6 0 0 1-6 6H9a6 6 0 0 1-6-6zM6 10V3h5" stroke="#1c1c1c" stroke-width="2" fill="none"/></svg></span><span class="feat"><svg width="30" height="22" viewBox="0 0 30 22"><path d="M4 16V10l4-6h14l4 6v6zM4 16v3M26 16v3" stroke="#1c1c1c" stroke-width="2" fill="none"/><circle cx="9" cy="12" r="1.6" fill="#1c1c1c"/><circle cx="21" cy="12" r="1.6" fill="#1c1c1c"/></svg></span></div>
  <p class="insp">Next Inspection:</p>
  <p class="date">Sat 2nd May 09:45 AM - 10:00 AM</p>
  <p class="price">$500,000+</p>
  <div class="bar"><span></span><span></span><span></span></div>
</article>

<article class="abs card" style="left:448px">
  <div class="photo" role="img" aria-label="White apartment tower with balconies" style="background:linear-gradient(#c8dbe9,#e8ecee 60%,#9fb4a2)"></div>
  <h4>WESTMERE</h4>
  <p class="addr">Level 3/77 Marlow Crescent Harcourt</p>
  <div class="feats"><span class="feat"><svg width="30" height="22" viewBox="0 0 30 22"><path d="M2 18V4M2 12h26v6M6 12V8h8v4" stroke="#1c1c1c" stroke-width="2" fill="none"/></svg></span><span class="feat"><svg width="30" height="22" viewBox="0 0 30 22"><path d="M3 10h24v4a6 6 0 0 1-6 6H9a6 6 0 0 1-6-6zM6 10V3h5" stroke="#1c1c1c" stroke-width="2" fill="none"/></svg></span><span class="feat"><svg width="30" height="22" viewBox="0 0 30 22"><path d="M4 16V10l4-6h14l4 6v6zM4 16v3M26 16v3" stroke="#1c1c1c" stroke-width="2" fill="none"/><circle cx="9" cy="12" r="1.6" fill="#1c1c1c"/><circle cx="21" cy="12" r="1.6" fill="#1c1c1c"/></svg></span></div>
  <p class="insp">Next Inspection:</p>
  <p class="date">Sat 2nd May 09:45 AM - 10:00 AM</p>
  <p class="price">$369,900+</p>
  <div class="bar"><span></span><span></span><span></span></div>
</article>

<article class="abs card" style="left:784px">
  <div class="photo" role="img" aria-label="Modern apartment building on a street corner" style="background:linear-gradient(#9cc0de,#b9c2c6 60%,#7d8a70)"></div>
  <h4>HARCOURT</h4>
  <p class="addr">Level 3/77 Marlow Crescent Harcourt</p>
  <div class="feats"><span class="feat"><svg width="30" height="22" viewBox="0 0 30 22"><path d="M2 18V4M2 12h26v6M6 12V8h8v4" stroke="#1c1c1c" stroke-width="2" fill="none"/></svg></span><span class="feat"><svg width="30" height="22" viewBox="0 0 30 22"><path d="M3 10h24v4a6 6 0 0 1-6 6H9a6 6 0 0 1-6-6zM6 10V3h5" stroke="#1c1c1c" stroke-width="2" fill="none"/></svg></span><span class="feat"><svg width="30" height="22" viewBox="0 0 30 22"><path d="M4 16V10l4-6h14l4 6v6zM4 16v3M26 16v3" stroke="#1c1c1c" stroke-width="2" fill="none"/><circle cx="9" cy="12" r="1.6" fill="#1c1c1c"/><circle cx="21" cy="12" r="1.6" fill="#1c1c1c"/></svg></span></div>
  <p class="insp">Next Inspection:</p>
  <p class="date">Sat 2nd May 09:45 AM - 10:00 AM</p>
  <p class="price">$500,000+</p>
  <div class="bar"><span></span><span></span><span></span></div>
</article>

<div class="abs arrow" style="left:20px;top:2480px"><svg width="18" height="18" viewBox="0 0 18 18"><path d="M12 3 5 9l7 6" stroke="#fff" stroke-width="3" fill="none"/></svg></div>
<div class="abs arrow" style="right:20px;top:2480px"><svg width="18" height="18" viewBox="0 0 18 18"><path d="M6 3l7 6-7 6" stroke="#fff" stroke-width="3" fill="none"/></svg></div>

<section class="abs team-bg"></section>
<h2 class="abs section-title script" style="top:2960px">Our Team</h2>
<svg class="abs divider" style="left:570px;top:3038px" viewBox="0 0 60 14"><rect x="0" y="6" width="60" height="2" fill="#d9a82e"/><rect x="24" y="2" width="12" height="10" fill="#fff" stroke="#d9a82e" stroke-width="2"/></svg>

<div class="abs member" style="left:112px">
  <div class="portrait" role="img" aria-label="Portrait of team member Leo Brandt"></div>
  <div class="info"><b>Leo Brandt</b><small><span>+61 5550 8474</span><span>0400 555 218</span></small></div>
</div>
<div class="abs member focus" style="left:362px">
  <div class="portrait" role="img" aria-label="Portrait of team member Nadia Ferris"></div>
  <div class="abs focus-card">
    <h5>Nadia Ferris</h5>
    <p>Business Relationship Manager<br>&amp; Senior Property Manager</p>
    <p>+61 5550 8474<br>0400 555 218</p>
    <span class="rm">READ MORE</span>
  </div>
</div>
<div class="abs member" style="left:612px">
  <div class="portrait" role="img" aria-label="Portrait of team member Clara Voss"></div>
  <div class="info"><b>Clara Voss</b><small><span>+61 5550 8474</span><span>0400 555 218</span></small></div>
</div>
<div class="abs member" style="left:862px">
  <div class="portrait" role="img" aria-label="Portrait of team member Irene Pold"></div>
  <div class="info"><b>Irene Pold</b><small><span>+61 5550 8474</span><span>0400 555 218</span></small></div>
</div>
<span class="abs btn" style="left:516px;top:3390px">VIEW MORE <span class="dot"><svg width="14" height="14" viewBox="0 0 14 14"><path d="M2 7h9M7 3l4 4-4 4" stroke="#d9a82e" stroke-width="2" fill="none"/></svg></span></span>

<h2 class="abs section-title script" style="top:3550px">Testimonials</h2>
<svg class="abs divider" style="left:570px;top:3628px" viewBox="0 0 60 14"><rect x="0" y="6" width="60" height="2" fill="#d9a82e"/><rect x="24" y="2" width="12" height="10" fill="#fff" stroke="#d9a82e" stroke-width="2"/></svg>

<div class="abs quote" style="left:112px">
  <div class="mark">“</div>
  <p>Clara is my best property manager! Always happy to answer my queries and keep us well informed at all stages. I will definitely recommend her to my friends.</p>
  <p class="who-said">- Tom Radley</p>
</div>
<div class="abs quote" style="left:628px">
  <div class="mark">“</div>
  <p>Very good service. Our property manager is very responsible, prompting and clear about details. They use the system to track everything so no need to worry about miscommunication. I strongly recommend this agent.</p>
  <p class="who-said">- Mia KELLER</p>
</div>
<div class="abs dots"><span></span><span class="on"></span><span></span></div>

<div class="abs skyline" role="img" aria-label="Grey city skyline silhouette"></div>

<footer class="abs footer">
  <div class="abs f-brand"><span class="brand-mark"></span><span><span class="brand-name">Ferndale</span><span class="brand-sub" style="color:#bbb">Estate Collective</span></span></div>
  <div class="abs f-social"><span></span><span></span><span></span></div>
  <div class="abs f-col" style="left:370px"><h6>QUICK LINKS</h6>HOME<br>ABOUT US<br>LEASING<br>BUY<br>SELL<br>BLOG</div>
  <div class="abs f-col" style="left:560px"><h6>LINKS</h6>COPYRIGHT<br>LEGAL<br>PRIVACY<br>ACCESSIBILITY<br>SITEMAP</div>
  <div class="abs f-col" style="left:740px"><h6>SUPPORT</h6>TEAM<br>ABOUT US<br>CAREERS<br>OUR VALUES<br>CONTACT US</div>
  <div class="abs f-col" style="left:900px;width:240px"><h6>CONTACT US</h6>
    <div class="contact-row"><svg width="16" height="18" viewBox="0 0 16 18"><path d="M8 17s6-6 6-10A6 6 0 0 0 2 7c0 4 6 10 6 10z" fill="#d9a82e"/><circle cx="8" cy="7" r="2" fill="#121212"/></svg><span>Address:<br>3/77 Marlow Crescent,<br>Harcourt, RV, 2912</span></div>
    <div class="contact-row"><svg width="16" height="16" viewBox="0 0 16 16"><path d="M3 1h3l1.5 4-2 1.5a9 9 0 0 0 4 4L11 8.5l4 1.5v3a2 2 0 0 1-2 2A13 13 0 0 1 1 3a2 2 0 0 1 2-2z" fill="#d9a82e"/></svg><span>Phone:<br>02 5550 1942</span></div>
    <div class="contact-row"><svg width="16" height="14" viewBox="0 0 16 14"><rect x="1" y="1" width="14" height="12" fill="#d9a82e"/><path d="M1 2l7 6 7-6" stroke="#121212" stroke-width="1.5" fill="none"/></svg><span>Email:<br>hello@ferndaleestate.com.au</span></div>
  </div>
  <p class="abs copy">©2022. All rights reserved.</p>
</footer>
<div class="abs chat"><svg width="24" height="22" viewBox="0 0 24 22"><path d="M2 3h20v12H9l-5 5v-5H2z" fill="#fff"/></svg></div>

</body>
</html>
```